Design Startseite Kanzlei-Homepage
Zielgruppe
Wir sind eine Rechtsanwaltskanzlei in Kempten (Allgäu) und regional sowie überregional in verschiedenen Rechtsgebieten tätig. Unsere Zielgruppe sind sowohl private als auch gewerbliche Mandanten.
Aufgabenstellung
Die bestehende Gestaltung wirkt derzeit aus unserer Sicht überholt. Insbesondere soll das bislang dominierende Rot vollständig entfallen.
Stattdessen stellen wir uns ein modernes, hochwertiges Erscheinungsbild vor, primär in dunklen Farbtönen (Anthrazit/Schwarz) kombiniert mit Beige- bzw. warmen Naturtönen. Ziel ist eine klare visuelle Anlehnung an unsere Kanzleiräumlichkeiten (siehe Fotos).
Die Webseite soll insgesamt moderner, klarer und visuell anspruchsvoller wirken, ohne an Seriosität und Zugänglichkeit einzubüßen. Die Balance zwischen hochwertigem Erscheinungsbild und mandantenorientierter Nutzerführung steht für uns im Vordergrund.

```html
<!DOCTYPE html>
<html lang="de">
<head>
<meta charset="utf-8">
<title>Kanzlei am Lindenhof – Rechtsanwälte in Kempten</title>
<link href="https://fonts.googleapis.com/css2?family=Inter:wght@300;400;500;600;700&display=swap" rel="stylesheet">
<style>
:root{
  --ink:#1d1e1f;
  --ink-deep:#151617;
  --band:#2a2a2a;
  --card:#262727;
  --beige:#c6a987;
  --beige-soft:#c9ad8b;
  --text:#f2efea;
  --muted:#bdb8b0;
  --line:#4a4640;
}
*{margin:0;padding:0;box-sizing:border-box}
html,body{width:1200px;height:4068px;overflow:hidden;background:var(--ink);font-family:"Inter",sans-serif;color:var(--text)}
.page{position:relative;width:1200px;height:4068px}
.abs{position:absolute}
.eyebrow{font-size:10px;letter-spacing:2.6px;text-transform:uppercase;color:var(--beige)}
.btn{position:absolute;display:flex;align-items:center;justify-content:center;font-size:11px;height:26px}
.btn-beige{background:var(--beige);color:#1b1b1b}
.btn-outline{border:1px solid #e8e4dd;color:#fff}
.btn-dark{background:#111;color:#fff}
.brand{font-weight:600;font-size:17px;letter-spacing:.5px;color:#fff;display:flex;align-items:center;gap:6px;white-space:nowrap}
.brand .dot{width:6px;height:6px;background:var(--beige)}

.hero{top:0;left:0;width:1200px;height:758px;background:linear-gradient(180deg,#2b2b2b 0%,#202020 55%,#1f1f1f 100%)}
.nav a{position:absolute;top:66px;font-size:11px;color:#e8e4dd;text-decoration:none}
.hero-title{left:100px;top:296px;font-weight:400;font-size:40px;line-height:48px}
.hero-title span{color:var(--beige)}
.hero-lead{left:100px;top:416px;width:420px;font-size:12.5px;line-height:16px;color:#e8e4dd}

.stats{top:758px;left:0;width:1200px;height:126px;background:var(--band)}
.stat{position:absolute;top:42px;display:flex;align-items:center;gap:14px;font-size:14px;line-height:17px}
.stat b{display:block;font-weight:400;color:var(--beige)}

.section-title{position:absolute;font-weight:400;font-size:27px;line-height:33px}
.card{position:absolute;background:var(--card);padding:28px 26px}
.card h3{font-weight:400;font-size:16px;color:var(--beige);margin:14px 0 18px}
.card p{font-size:13px;line-height:16px;color:#e8e4dd}
.card .more{position:absolute;left:26px;bottom:28px;font-size:10px;font-weight:700;color:var(--beige);text-decoration:underline;letter-spacing:.3px}
.review p{font-size:13px;line-height:16px;color:#e8e4dd;margin-top:18px}
.review .stars{color:var(--beige);font-size:19px;letter-spacing:5px}
.review .who{position:absolute;left:24px;bottom:24px;font-size:13px;font-weight:600;color:var(--beige)}
.review .who small{display:block;font-size:10px;font-weight:400;color:#ddd}

.address-card{left:523px;top:3387px;min-height:82px;background:var(--beige-soft);padding:15px 18px;color:#1b1b1b;white-space:nowrap}
.address-card .name{font-weight:600;font-size:14px}
.address-card .lines{font-size:12px;line-height:15px;margin-top:4px}

.footer h4{font-size:13px;font-weight:600;color:var(--beige);margin-bottom:12px}
.footer li{list-style:none;font-size:11px;line-height:13.5px;color:#e0dcd5;white-space:nowrap}
</style>
</head>
<body>
<div class="page">

<section class="abs hero" role="img" aria-label="Gedämpftes Foto des Empfangsbereichs der Kanzlei"></section>
<div class="abs brand" style="left:100px;top:62px">KANZLEI <span class="dot"></span> LINDENHOF</div>
<nav class="nav">
  <a style="left:352px">Kanzlei</a><a style="left:437px">Anwälte</a><a style="left:525px">Rechtsgebiete</a><a style="left:644px">Karriere</a><a style="left:733px">News</a><a style="left:811px">Kontakt</a>
</nav>
<div class="btn btn-beige" style="left:970px;top:59px;width:131px">Termin vereinbaren</div>
<div class="abs eyebrow" style="left:100px;top:248px">Ihre Rechtsanwälte in Kempten</div>
<h1 class="abs hero-title">Rechtliche Klarheit.<br><span>Persönlich. Kompetent.</span></h1>
<p class="abs hero-lead">Wir beraten und vertreten Privatpersonen sowie Unternehmen in allen wesentlichen Rechtsfragen – engagiert, lösungsorientiert und auf Augenhöhe.</p>
<div class="btn btn-beige" style="left:100px;top:565px;width:131px">Termin vereinbaren</div>
<div class="btn btn-outline" style="left:272px;top:565px;width:131px">Unsere Kanzlei</div>

<section class="abs stats">
  <div class="stat" style="left:90px">
    <svg width="38" height="42" viewBox="0 0 38 42"><path d="M19 1 37 11v20L19 41 1 31V11z" fill="var(--beige)"/><circle cx="19" cy="16" r="5" fill="var(--band)"/><path d="M10 30c1-6 5-8 9-8s8 2 9 8z" fill="var(--band)"/></svg>
    <div><b>20+</b>Jahre Erfahrung</div>
  </div>
  <div class="stat" style="left:392px">
    <svg width="40" height="30" viewBox="0 0 40 30" fill="none" stroke="var(--beige)" stroke-width="3"><circle cx="13" cy="9" r="6"/><circle cx="28" cy="9" r="6"/><path d="M2 28c1-7 5-10 11-10s9 3 10 10M18 18c2-1 4-1 10 0 6 0 9 4 10 10"/></svg>
    <div><b>1500+</b>Mandanten</div>
  </div>
  <div class="stat" style="left:664px">
    <svg width="42" height="42" viewBox="0 0 42 42"><circle cx="21" cy="21" r="18" fill="none" stroke="var(--beige)" stroke-width="5"/></svg>
    <div><b>4.9 / 5</b>Portal Bewertung</div>
  </div>
  <div class="stat" style="left:980px">
    <svg width="34" height="44" viewBox="0 0 34 44"><path d="M17 2C9 2 3 8 3 16c0 11 14 26 14 26s14-15 14-26C31 8 25 2 17 2z" fill="none" stroke="var(--beige)" stroke-width="4"/><circle cx="17" cy="16" r="5" fill="var(--beige)"/></svg>
    <div><b>Kempten</b><span style="font-size:15px">Im Allgäu</span></div>
  </div>
</section>

<section class="abs" style="top:884px;left:0;width:1200px;height:750px;background:var(--ink)"></section>
<div class="abs eyebrow" style="left:96px;top:980px">Unsere Rechtsgebiete</div>
<h2 class="section-title" style="left:96px;top:1006px">Kompetenz, die den<br>Unterschied macht.</h2>

<div class="card" style="left:440px;top:979px;width:211px;height:264px">
  <svg width="40" height="28" viewBox="0 0 40 30" fill="none" stroke="#fff" stroke-width="3"><circle cx="13" cy="9" r="6"/><circle cx="28" cy="9" r="6"/><path d="M2 28c1-7 5-10 11-10s9 3 10 10M18 18c2-1 4-1 10 0 6 0 9 4 10 10"/></svg>
  <h3>Arbeitsrecht</h3>
  <p>Beratung und Vertretung für Arbeitgeber und Arbeitnehmer in allen Fragen des Arbeitsverhältnisses.</p>
  <span class="more">MEHR ERFAHREN</span>
</div>
<div class="card" style="left:666px;top:979px;width:212px;height:264px">
  <svg width="36" height="30" viewBox="0 0 36 30" fill="#fff"><circle cx="7" cy="5" r="4"/><circle cx="29" cy="5" r="4"/><circle cx="18" cy="11" r="3"/><rect x="3" y="11" width="8" height="18"/><rect x="25" y="11" width="8" height="18"/><rect x="15" y="16" width="6" height="13"/></svg>
  <h3>Familienrecht</h3>
  <p>Einfühlsame Unterstützung in allen Bereichen des Familienrechts – von Scheidung bis Unterhalt.</p>
  <span class="more">MEHR ERFAHREN</span>
</div>
<div class="card" style="left:894px;top:979px;width:210px;height:264px">
  <svg width="32" height="32" viewBox="0 0 32 32"><rect x="2" y="8" width="28" height="22" rx="5" fill="#fff"/><rect x="8" y="2" width="16" height="14" rx="2" fill="#fff" stroke="var(--card)" stroke-width="2"/><path d="M11 9l4 3 6-6" stroke="var(--card)" stroke-width="2" fill="none"/></svg>
  <h3>Erbrecht</h3>
  <p>Gestaltung, Beratung und Vertretung bei Erbfällen, Testament und Pflichtteilsansprüchen.</p>
  <span class="more">MEHR ERFAHREN</span>
</div>
<div class="card" style="left:440px;top:1258px;width:211px;height:263px">
  <svg width="24" height="30" viewBox="0 0 24 30"><rect x="1" y="1" width="22" height="29" fill="#fff"/><g fill="var(--card)"><rect x="5" y="5" width="4" height="4"/><rect x="15" y="5" width="4" height="4"/><rect x="5" y="13" width="4" height="4"/><rect x="15" y="13" width="4" height="4"/><rect x="9" y="22" width="6" height="8"/></g></svg>
  <h3>Baurecht</h3>
  <p>Kompetente Begleitung bei Bauvorhaben, Verträgen und Streitigkeiten rund um die Immobilie.</p>
  <span class="more">MEHR ERFAHREN</span>
</div>
<div class="card" style="left:666px;top:1258px;width:212px;height:263px">
  <svg width="34" height="28" viewBox="0 0 34 28"><path d="M5 12 9 3h16l4 9h3v12h-5v4h-4v-4H10v4H6v-4H2V12z" fill="#fff"/><rect x="10" y="6" width="14" height="6" fill="var(--card)"/><circle cx="8" cy="18" r="2.5" fill="var(--card)"/><circle cx="26" cy="18" r="2.5" fill="var(--card)"/></svg>
  <h3>Verkehrsrecht</h3>
  <p>Durchsetzung Ihrer Ansprüche nach Unfällen, Bußgeldverfahren und in allen Fragen des Verkehrsrechts.</p>
  <span class="more">MEHR ERFAHREN</span>
</div>
<div class="card" style="left:894px;top:1258px;width:210px;height:263px">
  <svg width="26" height="32" viewBox="0 0 26 32"><rect x="1" y="4" width="24" height="27" rx="2" fill="#fff"/><rect x="8" y="1" width="10" height="6" rx="1" fill="#fff" stroke="var(--card)" stroke-width="1.5"/><g stroke="var(--card)" stroke-width="2.5"><path d="M5 14h16M5 20h16M5 26h10"/></g></svg>
  <h3>Wirtschaftsrecht</h3>
  <p>Rechtsichere Lösungen für Unternehmen – von der Gründung bis zur Vertragsgestaltung.</p>
  <span class="more">MEHR ERFAHREN</span>
</div>

<section class="abs" style="top:1634px;left:0;width:1200px;height:514px;background:linear-gradient(90deg,#1f2021,#262626)" role="img" aria-label="Abgedunkeltes Foto der Kanzleiflure"></section>
<div class="abs" style="top:1634px;left:265px;width:667px;height:514px;background:linear-gradient(180deg,#2f2f2e 0%,#3a3937 45%,#242424 100%);border-left:2px solid #6b5c49;border-right:2px solid #6b5c49" role="img" aria-label="Foto des Wartebereichs mit Sitzbank und Wandbild"></div>
<svg class="abs" style="left:735px;top:1965px" width="110" height="110" viewBox="0 0 110 110">
  <defs><path id="ring" d="M55 55m-44 0a44 44 0 1 1 88 0a44 44 0 1 1-88 0"/></defs>
  <circle cx="55" cy="55" r="28" fill="rgba(120,120,120,.55)"/>
  <path d="M48 43v24l20-12z" fill="#1c1c1c"/>
  <text font-family="Inter,sans-serif" font-size="11" fill="#ddd" letter-spacing="1"><textPath href="#ring" startOffset="2%">Machen Sie einen Rundgang</textPath></text>
</svg>

<div class="abs eyebrow" style="left:96px;top:2283px">Das sagen unsere Mandanten</div>
<h2 class="section-title" style="left:96px;top:2310px">Vertrauen, das<br>verbindet.</h2>
<div class="card review" style="left:440px;top:2282px;width:211px;height:253px;padding:24px">
  <div class="stars">★★★★★</div>
  <p>Kompetent, zuverlässig und jederzeit ansprechbar. Ich habe mich von Anfang an sehr gut aufgehoben gefühlt.</p>
  <div class="who">Jonas R.<small>Unternehmer</small></div>
</div>
<div class="card review" style="left:666px;top:2282px;width:212px;height:253px;padding:24px">
  <div class="stars">★★★★★</div>
  <p>Vielen Dank für die erstklassige Beratung und die schnelle Lösung meines Anliegens. Absolute Empfehlung!</p>
  <div class="who">Petra L.<small>Privatmandantin</small></div>
</div>
<div class="card review" style="left:894px;top:2282px;width:210px;height:253px;padding:24px">
  <div class="stars">★★★★★</div>
  <p>Die Kanzlei am Lindenhof ist für uns seit Jahren ein verlässlicher Partner in allen rechtlichen Fragen.</p>
  <div class="who">Stefan W.<small>Geschäftsführer</small></div>
</div>

<section class="abs" style="top:2665px;left:0;width:714px;height:498px;background:linear-gradient(180deg,#2c2b29 0%,#343230 50%,#1c1c1c 100%)" role="img" aria-label="Foto des Kanzleiempfangs als Filmvorschau"></section>
<div class="abs eyebrow" style="left:96px;top:2743px">Kanzlei am Lindenhof</div>
<h2 class="section-title" style="left:96px;top:2768px">Unsere Kanzlei in<br>einem Film.</h2>
<svg class="abs" style="left:96px;top:3013px" width="76" height="76" viewBox="0 0 76 76"><circle cx="38" cy="38" r="38" fill="var(--beige)"/><path d="M30 25v26l22-13z" fill="#1a1a1a"/></svg>

<section class="abs" style="top:2665px;left:714px;width:486px;height:498px;background:var(--beige-soft)"></section>
<div class="abs eyebrow" style="left:794px;top:2743px;color:#2a2520">Lassen Sie uns sprechen</div>
<h2 class="section-title" style="left:794px;top:2780px;color:#1b1b1b">Wir sind für<br>Sie da.</h2>
<p class="abs" style="left:794px;top:2862px;width:230px;font-size:12.5px;line-height:15px;color:#1b1b1b">Vereinbaren Sie ein unverbindliches Erstgespräch – wir nehmen uns Zeit für Ihr Anliegen.</p>
<div class="btn btn-dark" style="left:794px;top:3002px;width:131px">Termin vereinbaren</div>

<section class="abs" style="top:3163px;left:0;width:1200px;height:532px;background:radial-gradient(ellipse at 50% 50%,#34312d 0%,#262523 70%,#1f1e1d 100%)" role="img" aria-label="Abgedunkelte Landkarte der Region um Kempten"></section>
<svg class="abs" style="left:454px;top:3386px" width="56" height="76" viewBox="0 0 56 76"><path d="M28 3C14 3 3 14 3 28c0 19 25 45 25 45s25-26 25-45C53 14 42 3 28 3z" fill="none" stroke="var(--beige)" stroke-width="6"/><circle cx="28" cy="27" r="9" fill="var(--beige)"/></svg>
<div class="abs address-card">
  <div class="name">KANZLEI AM LINDENHOF</div>
  <div class="lines">Parkstraße 14<br>87439 Kempten (Allgäu)</div>
</div>

<footer class="abs footer" style="top:3695px;left:0;width:1200px;height:373px;background:var(--ink)">
  <div class="abs brand" style="left:100px;top:83px;font-size:22px">KANZLEI <span class="dot" style="width:8px;height:8px"></span> LINDENHOF</div>
  <p class="abs" style="left:100px;top:127px;width:220px;font-size:12.5px;line-height:15px;color:#e0dcd5">rechtsanwälte in kempten (allgäu) kompetent, persönlich, lösungsorientiert.</p>
  <div class="abs" style="left:416px;top:80px;width:1px;height:120px;background:#7a6a56"></div>
  <div class="abs" style="left:561px;top:88px"><h4>kanzlei</h4><ul><li>über uns</li><li>team</li><li>karriere</li><li>news</li></ul></div>
  <div class="abs" style="left:675px;top:88px"><h4>Rechtsgebiete</h4><ul><li>arbeitsrecht</li><li>familienrecht</li><li>erbrecht</li><li>baurecht</li><li>verkehrsrecht</li><li>wirtschaftsrecht</li></ul></div>
  <div class="abs" style="left:837px;top:88px"><h4>Service</h4><ul><li>erstberatung</li><li>downloads</li><li>faq</li></ul></div>
  <div class="abs" style="left:970px;top:88px"><h4>Kontakt</h4><ul><li>parkstraße 14</li><li>87439 kempten (allgäu)</li><li>&nbsp;</li><li>0831 204 77 0</li><li>info@kanzlei-lindenhof.de</li></ul></div>
  <div class="abs" style="left:100px;top:243px;width:1004px;height:1px;background:#6d5f4f"></div>
  <div class="abs" style="left:100px;top:278px;font-size:12px;color:#a9a39a">© 2026 kanzlei am lindenhof</div>
  <div class="abs" style="left:876px;top:281px;font-size:10px;color:#8e8880;display:flex;gap:36px"><span>impressum</span><span>datenschutz</span><span>sitemap</span></div>
</footer>

</div>
</body>
</html>
```